NEW Wordpress Website Design for a Dynamic Long Term Healthcare Company in Hawaii

I would like a new website design for my current company, Marlow Health Collective, which has two different brands - Marlow Homecare and Marlow Senior Living. You can see the current website at www.marlowhealth-example.com. The website should be built using Wordpress Software and the Framewise theme. The website should have a local Hawaii island/tropical feel, but look professional for healthcare. I'm looking for something fresh, and want the designer to select colors, styles, etc.

In the Header, on all pages, I would like a menu that includes Home Care, Senior Living, Rates, and About Us.
Under each of the Header Menu Titles, I would like these drop downs included:
Home Care (drop down pages)- Nurse Aide Care, 24-Hour Home Care, Skilled Nursing, Lifestyle Aide, Hospice at Home, Bathing & Meal Service.
Senior Living (drop down pages) - Long-Term Stay, Short-Term Stay.
Rates (drop down page) - Rates.
About Us (drop down pages) - Our Mission, Ohana Talk, About Dana Marlow.

In the footer, on all pages, you should include the address: 248 Pueo Lane, Suite 310, Honolulu, HI 96817. Phone number: 808-555-0172
The footer should also include buttons for a page called Learn, Caregiver Jobs, and each of the service page links to include: Nurse Aide Care, 24-Hour Home Care, Skilled Nursing, Lifestyle Aide, Hospice at Home, Bathing & Meal Service.
Please don't take the current website and redesign a few aspects. I'm looking for a completely different look and feel.

Target Market(s)

40-80 year olds

Industry/Entity Type

Long Term Healthcare

Coding

Coded - Design and coding required

Requirements
Should not have
• Our existing website as a template. We are looking for a complete redesign. Thank you.

```html
<!DOCTYPE html>
<html lang="en">
<head>
<meta charset="utf-8">
<title>Marlow Health Collective</title>
<link href="https://fonts.googleapis.com/css2?family=Inter:wght@400;500;600;700;800&display=swap" rel="stylesheet">
<style>
:root{
  --coral:#f5837a;
  --coral-dark:#ee6f66;
  --blush:#fdf0ef;
  --ink:#1b1b1b;
  --text:#333;
  --muted:#9a9a9a;
  --line:#e6e6e6;
  --white:#fff;
}
*{box-sizing:border-box;margin:0;padding:0}
html,body{width:1200px;height:4069px;overflow:hidden;background:var(--white)}
body{font-family:'Inter',sans-serif;color:var(--ink);position:relative}
.wrap{position:absolute;left:90px;width:1020px}
.btn{display:inline-flex;align-items:center;justify-content:center;background:var(--coral);color:var(--white);font-weight:600;font-size:13px;border-radius:20px;height:34px;padding:0 20px}
.h2{font-size:40px;font-weight:700;letter-spacing:-.2px}

/* header */
.site-header{top:0;height:90px;display:flex;align-items:center;justify-content:space-between}
.brand-set{display:flex;gap:18px;align-items:center}
.brand{display:flex;align-items:center;gap:6px;font-size:13px;font-weight:600;color:var(--coral)}
.brand i{width:12px;height:12px;background:var(--coral);border-radius:50%;display:block}
.main-nav{display:flex;align-items:center;gap:26px;font-size:13px;font-weight:600}
.main-nav span{display:flex;align-items:center;gap:6px}
.main-nav .active{color:var(--coral)}
.main-nav .btn{border-radius:6px;height:34px;padding:0 14px}

/* hero */
.hero{top:114px;height:570px;border-radius:14px;overflow:hidden;background:linear-gradient(180deg,#7a6a4e 0%,#b9a27a 35%,#a47b55 70%,#5e4630 100%)}
.hero-photo{position:absolute;inset:0;background:linear-gradient(180deg,rgba(60,45,30,.25),rgba(40,30,20,.35))}
.hero-title{position:absolute;top:176px;width:100%;text-align:center;color:var(--white);font-size:30px;font-weight:700;line-height:38px}
.hero-sub{position:absolute;top:273px;width:100%;text-align:center;color:var(--white);font-size:12.5px}
.book-card{position:absolute;left:346px;top:344px;width:327px;height:198px;background:var(--blush);border-radius:10px;padding:20px}
.book-card h3{text-align:center;font-size:16px;font-weight:600;margin-bottom:22px}
.book-card label{font-size:12px;color:var(--muted)}
.select{margin-top:8px;height:38px;background:var(--white);border-radius:4px;display:flex;align-items:center;justify-content:space-between;padding:0 14px;font-size:12px;font-weight:500}
.book-card .btn{width:100%;margin-top:20px;height:34px}

/* about */
.about{top:765px;height:412px}
.about-photo{position:absolute;left:0;top:0;width:414px;height:412px;border-radius:6px;background:linear-gradient(135deg,#8a5a3a,#c9b27a 45%,#9db27a)}
.about-text{position:absolute;left:521px;top:0;width:499px}
.about-text h2{font-size:43px;font-weight:700;line-height:48px}
.about-text p{margin-top:30px;font-size:13px;line-height:22px;color:var(--text)}
.about-text .btn{margin-top:40px}

/* services */
.services{top:1255px;height:610px}
.service-list{position:absolute;left:0;top:88px;width:500px}
.svc{display:flex;justify-content:space-between;align-items:center;font-size:20px;font-weight:600;height:34px}
.svc-card{background:var(--blush);border-radius:12px;padding:24px 20px;margin:22px 0 22px}
.svc-card h3{font-size:20px;font-weight:600}
.svc-card p{margin-top:14px;font-size:13px;line-height:22px;color:var(--text)}
.svc-card .btn{margin-top:18px;height:32px}
.service-list .gap{height:19px}
.service-photo{position:absolute;left:607px;top:91px;width:413px;height:512px;border-radius:6px;background:linear-gradient(160deg,#d9d96a,#c9c37a 40%,#5aa0a6 75%,#8c7a55)}

/* why */
.why{top:1935px;height:330px}
.why-grid{position:absolute;top:92px;display:flex;gap:20px}
.why-card{width:240px;height:231px;background:var(--coral);border-radius:6px;padding:18px 20px;color:var(--white)}
.why-card h3{font-size:22px;font-weight:700;line-height:28px;height:106px}
.why-card svg{display:block;margin:0 auto}

/* stories */
.stories{top:2335px;height:560px}
.story-row{position:absolute;top:92px;display:flex;gap:20px}
.portrait{width:240px;height:240px;border-radius:6px}
.p1{background:linear-gradient(160deg,#6d5a40,#b99a6a 50%,#3c3128)}
.p3{background:linear-gradient(160deg,#d9462f,#b57b5a 55%,#f0a030)}
.story-main{display:flex;width:498px;height:377px;border-radius:6px;overflow:hidden;background:var(--blush)}
.p2{width:240px;height:377px;background:linear-gradient(160deg,#a7b5b8,#6f7f82 45%,#3b3b3b)}
.quote{width:258px;padding:30px 22px 0 20px;font-size:14.5px;line-height:23.3px;color:var(--text)}
.quote b{display:block;margin-top:14px;font-size:18px;font-weight:600;color:var(--ink)}
.arrows{position:absolute;top:496px;left:447px;display:flex;gap:20px}
.arrows span{width:52px;height:52px;border:2px solid var(--ink);border-radius:50%;display:flex;align-items:center;justify-content:center}

/* contact */
.contact{top:2966px;height:701px}
.contact h2{position:absolute;top:0;font-size:56px;font-weight:700;line-height:64px}
.info{position:absolute;left:0;display:flex;align-items:center;gap:16px;font-size:17px}
.info i{width:40px;height:38px;background:var(--coral);border-radius:4px;display:flex;align-items:center;justify-content:center}
.form-card{position:absolute;left:521px;top:0;width:499px;height:701px;background:var(--blush);border-radius:12px;padding:26px 27px}
.form-card h3{text-align:center;font-size:28px;font-weight:600}
.form-card .lead{text-align:center;font-size:16px;margin-top:10px;margin-bottom:22px}
.field{background:var(--white);height:40px;border-radius:3px;font-size:12.5px;color:#b5b5b5;display:flex;align-items:center;padding:0 14px;margin-bottom:22px}
.row{display:flex;gap:20px}
.row .field{flex:1}
.code{background:#f7c9c4;color:var(--ink);width:62px;height:40px;border-radius:3px 0 0 3px;display:flex;align-items:center;justify-content:center;gap:4px;font-size:12.5px}
.tall{height:134px;align-items:flex-start;padding-top:14px}
.check{display:flex;align-items:center;gap:10px;font-size:11.5px;font-weight:500;margin-top:-2px}
.check i{width:18px;height:18px;background:var(--coral);border-radius:3px;display:flex;align-items:center;justify-content:center}
.form-card .btn{width:100%;height:40px;border-radius:20px;margin-top:22px}
.fine{margin-top:22px;text-align:center;font-size:12.5px;line-height:22px;color:#888}

/* footer */
.site-footer{top:3740px;height:330px}
.foot-brands{position:absolute;left:0;top:30px;display:flex;flex-direction:column;gap:12px}
.col{position:absolute;top:0}
.col h4{font-size:16px;font-weight:600;margin-bottom:14px}
.col a{display:block;font-size:13px;color:var(--ink);text-decoration:none;line-height:31.6px}
.foot-line{position:absolute;top:257px;left:0;width:1020px;height:1px;background:var(--line)}
.copy{position:absolute;top:287px;width:100%;text-align:center;font-size:13px}
</style>
</head>
<body>

<header class="wrap site-header">
  <div class="brand-set">
    <span class="brand"><i></i>Marlow Homecare</span>
    <span class="brand"><i></i>Marlow Senior Living</span>
  </div>
  <nav class="main-nav">
    <span class="active">Home Care <svg width="10" height="6" viewBox="0 0 10 6"><path d="M1 1l4 4 4-4" fill="none" stroke="currentColor" stroke-width="1.6"/></svg></span>
    <span>Senior Living <svg width="10" height="6" viewBox="0 0 10 6"><path d="M1 1l4 4 4-4" fill="none" stroke="currentColor" stroke-width="1.6"/></svg></span>
    <span>Rates <svg width="10" height="6" viewBox="0 0 10 6"><path d="M1 1l4 4 4-4" fill="none" stroke="currentColor" stroke-width="1.6"/></svg></span>
    <span>About Us <svg width="10" height="6" viewBox="0 0 10 6"><path d="M1 1l4 4 4-4" fill="none" stroke="currentColor" stroke-width="1.6"/></svg></span>
    <span class="btn">Contact Us</span>
  </nav>
</header>

<section class="wrap hero">
  <div class="hero-photo" role="img" aria-label="Photo of a caregiver and two senior women sharing a happy moment in a sunny living room"></div>
  <h1 class="hero-title">Our Commitment to Your Health at<br>Home and in Senior Living</h1>
  <p class="hero-sub">Experience Personalized and Professional Care with the Warmth and Spirit of Hawaii</p>
  <div class="book-card">
    <h3>Home Care</h3>
    <label>Service</label>
    <div class="select">Nurse Aide Care <svg width="11" height="7" viewBox="0 0 10 6"><path d="M1 1l4 4 4-4" fill="none" stroke="#222" stroke-width="1.4"/></svg></div>
    <span class="btn">Schedule Care</span>
  </div>
</section>

<section class="wrap about">
  <div class="about-photo" role="img" aria-label="Photo of a caregiver serving a meal to a senior couple at their dining table"></div>
  <div class="about-text">
    <h2>Caring for Your Family with Love and Professionalism.</h2>
    <p>We are dedicated to delivering personalized care that addresses the unique needs of each client, fostering a sense of trust, respect, and dignity. Our team of skilled healthcare professionals is committed to creating a supportive environment that not only attends to medical needs but also promotes emotional and social well-being.</p>
    <span class="btn">Contact Us</span>
  </div>
</section>

<section class="wrap services">
  <h2 class="h2">Our Service</h2>
  <div class="service-list">
    <div class="svc">Nurse Aide Care <svg width="18" height="18" viewBox="0 0 18 18"><path d="M3 15L15 3M6 3h9v9" fill="none" stroke="#1b1b1b" stroke-width="2"/></svg></div>
    <div class="svc-card">
      <h3>24-Hour Home Care</h3>
      <p>Provides continuous, around-the-clock care for individuals needing long-term assistance due to chronic conditions, post-surgery recovery, or special health needs.</p>
      <span class="btn">Learn more</span>
    </div>
    <div class="svc">Skilled Nursing <svg width="18" height="18" viewBox="0 0 18 18"><path d="M3 15L15 3M6 3h9v9" fill="none" stroke="#1b1b1b" stroke-width="2"/></svg></div>
    <div class="gap"></div>
    <div class="svc">Lifestyle Aide <svg width="18" height="18" viewBox="0 0 18 18"><path d="M3 15L15 3M6 3h9v9" fill="none" stroke="#1b1b1b" stroke-width="2"/></svg></div>
    <div class="gap"></div>
    <div class="svc">Hospice at Home <svg width="18" height="18" viewBox="0 0 18 18"><path d="M3 15L15 3M6 3h9v9" fill="none" stroke="#1b1b1b" stroke-width="2"/></svg></div>
    <div class="gap"></div>
    <div class="svc">Bathing &amp; Meal Service <svg width="18" height="18" viewBox="0 0 18 18"><path d="M3 15L15 3M6 3h9v9" fill="none" stroke="#1b1b1b" stroke-width="2"/></svg></div>
  </div>
  <div class="service-photo" role="img" aria-label="Photo of a nurse helping a senior man sit up on his bed"></div>
</section>

<section class="wrap why">
  <h2 class="h2">Why Choose Us</h2>
  <div class="why-grid">
    <div class="why-card"><h3>Over 10+ years of care experience.</h3>
      <svg width="72" height="72" viewBox="0 0 72 72" fill="none" stroke="#fff" stroke-width="3.5"><circle cx="36" cy="36" r="20"/><ellipse cx="36" cy="36" rx="32" ry="11" transform="rotate(-35 36 36)"/></svg></div>
    <div class="why-card"><h3>Highly personalized services.</h3>
      <svg width="72" height="72" viewBox="0 0 72 72" fill="none" stroke="#fff" stroke-width="3.5"><circle cx="30" cy="20" r="12"/><ellipse cx="28" cy="56" rx="18" ry="10"/><path d="M50 40c-6-5-6-10-2-11 2-1 3 1 2 2 1-1 3-3 5-1 3 2 0 6-5 10z"/></svg></div>
    <div class="why-card"><h3>Licensed healthcare professionals.</h3>
      <svg width="72" height="72" viewBox="0 0 72 72" fill="none" stroke="#fff" stroke-width="3.5"><rect x="8" y="8" width="56" height="44" rx="6"/><path d="M20 22h32M24 32h24"/><circle cx="36" cy="54" r="7"/><path d="M30 58l-4 10 10-4 10 4-4-10"/></svg></div>
    <div class="why-card"><h3>Family-focused, wellness-driven approach.</h3>
      <svg width="72" height="72" viewBox="0 0 72 72" fill="none" stroke="#fff" stroke-width="3.5"><circle cx="36" cy="20" r="10"/><ellipse cx="36" cy="52" rx="16" ry="10"/><path d="M18 20a6 6 0 1 0 0 .1M54 20a6 6 0 1 0 0 .1M10 50c0-6 6-8 10-8M62 50c0-6-6-8-10-8"/></svg></div>
  </div>
</section>

<section class="wrap stories">
  <h2 class="h2">Stories from Our Family</h2>
  <div class="story-row">
    <div class="portrait p1" role="img" aria-label="Portrait photo of a smiling family member outdoors"></div>
    <div class="story-main">
      <div class="p2" role="img" aria-label="Portrait photo of the testimonial author"></div>
      <div class="quote">"Marlow Health Collective has been a true blessing for our family. The caregivers are not only professional but also incredibly compassionate. Knowing that my loved one is receiving 24-hour care from such dedicated people gives us peace of mind. Their attention to detail and personal touch truly make a difference.<b>- Noelani Kekumu</b></div>
    </div>
    <div class="portrait p3" role="img" aria-label="Portrait photo of a family member in a cap"></div>
  </div>
  <div class="arrows">
    <span><svg width="22" height="16" viewBox="0 0 22 16"><path d="M21 8H2M8 1L1 8l7 7" fill="none" stroke="#1b1b1b" stroke-width="2"/></svg></span>
    <span><svg width="22" height="16" viewBox="0 0 22 16"><path d="M1 8h19M14 1l7 7-7 7" fill="none" stroke="#1b1b1b" stroke-width="2"/></svg></span>
  </div>
</section>

<section class="wrap contact">
  <h2>We're here to<br>serve you<br>anytime</h2>
  <div class="info" style="top:230px"><i><svg width="22" height="22" viewBox="0 0 24 24"><path d="M5 3h4l2 5-3 2a12 12 0 0 0 6 6l2-3 5 2v4a2 2 0 0 1-2 2A18 18 0 0 1 3 5a2 2 0 0 1 2-2z" fill="none" stroke="#fff" stroke-width="1.8"/></svg></i>(808) 555-0172</div>
  <div class="info" style="top:290px"><i><svg width="22" height="22" viewBox="0 0 24 24"><path d="M12 22s7-7 7-12a7 7 0 0 0-14 0c0 5 7 12 7 12z" fill="none" stroke="#fff" stroke-width="1.8"/><circle cx="12" cy="10" r="2.5" fill="none" stroke="#fff" stroke-width="1.8"/></svg></i>248 Pueo Lane, Suite 310, Honolulu, HI 96817</div>
  <div class="form-card">
    <h3>Care Consultation</h3>
    <p class="lead">Schedule a complimentary Care Consultation</p>
    <div class="row"><div class="field">First name*</div><div class="field">Last name</div></div>
    <div class="field">Email*</div>
    <div class="field" style="padding:0"><span class="code">+1 <svg width="9" height="6" viewBox="0 0 10 6"><path d="M1 1l4 4 4-4" fill="none" stroke="#222" stroke-width="1.6"/></svg></span><span style="padding-left:14px">Phone number</span></div>
    <div class="field">How did you hear about us?</div>
    <div class="field tall">How can we help?</div>
    <div class="check"><i><svg width="11" height="9" viewBox="0 0 11 9"><path d="M1 4.5l3 3 6-6" fill="none" stroke="#fff" stroke-width="1.8"/></svg></i>Get notifications via email</div>
    <span class="btn">Submit</span>
    <p class="fine">You agree to receive future emails and understand you may opt-out<br>at any time</p>
  </div>
</section>

<footer class="wrap site-footer">
  <div class="foot-brands">
    <span class="brand"><i></i>Marlow Homecare</span>
    <span class="brand"><i></i>Marlow Health Collective</span>
    <span class="brand"><i></i>Marlow Senior Living</span>
  </div>
  <div class="col" style="left:345px"><h4>Service</h4>
    <a>Nurse Aide Care</a><a>24-Hour Home Care</a><a>Skilled Nursing</a><a>Lifestyle Aide</a><a>Hospice at Home</a><a>Bathing &amp; Meal Service</a></div>
  <div class="col" style="left:605px"><h4>Company</h4>
    <a>Learn</a><a>About Us</a><a>Caregiver Jobs</a><a>Contact us</a><a>Privacy and Policy</a></div>
  <div class="col" style="left:865px"><h4>Social Media</h4>
    <a>Ohana Circle</a><a>Island Feed</a><a>Video Lanai</a><a>Photo Reef</a></div>
  <div class="foot-line"></div>
  <p class="copy">© 2023 Marlow Health Collective. All Rights Reserved.</p>
</footer>

</body>
</html>
```